Business Landing Page for SEO Company

Need the landing page of the website designed - I will provide the copy, will need to include details of my company and the services offered, about us, testimonials, faq, etc., and all these elements will need to be arranged graphically on the page.

I want something similar to this: https://torvanequill.com/

Not in terms of color or theme or anything, but we offer a similar service and want to display similar information.

Th services we provide are:

Premium Links
Monthly Links Subscription
Link Insertions

Need to advertise them on the front page. Additionally need a place for testimonials, company details, etc.,

We already have logo for the website. Please use the attached file to insert the logo within the overal design.

Target Market(s)

SEO marketers and agencies

Number of Pages Required

1 page

```html
<!DOCTYPE html>
<html lang="en">
<head>
<meta charset="utf-8">
<title>Zentory – Done-For-You Link Building</title>
<link rel="stylesheet" href="https://fonts.googleapis.com/css2?family=Rubik:wght@400;500;700;800&family=Open+Sans:wght@400;600&display=swap">
<style>
:root{
  --blue:#1f6fd6;
  --blue-dark:#165bbd;
  --blue-light:#3b8ef0;
  --orange:#f57c00;
  --ink:#1b1b2b;
  --text:#555a66;
  --pale:#f2f4f9;
  --white:#ffffff;
  --line:#c9d7ee;
}
*{box-sizing:border-box;margin:0;padding:0}
html,body{width:1200px;height:3801px;overflow:hidden}
body{position:relative;background:var(--white);font-family:"Open Sans",sans-serif;color:var(--text)}
.abs{position:absolute}
.heading{font-family:"Rubik",sans-serif;font-weight:800;color:var(--blue);letter-spacing:.5px}
.eyebrow{font-family:"Rubik",sans-serif;font-size:16px;color:var(--orange);letter-spacing:.5px}
.btn{display:flex;align-items:center;gap:18px;background:var(--orange);color:var(--white);font-family:"Rubik",sans-serif;font-weight:500;font-size:12px;letter-spacing:.5px;padding:0 14px;height:42px;border-radius:3px}
.wordmark{font-family:"Rubik",sans-serif;font-weight:500;color:var(--blue)}

/* header */
.site-header{left:0;top:0;width:1200px;height:112px}
.site-header .wordmark{left:98px;top:20px;font-size:60px}
.main-nav{left:384px;top:46px;display:flex;gap:34px;font-family:"Rubik",sans-serif;font-weight:500;font-size:16px;color:var(--ink)}
.login{left:964px;top:41px;width:100px;height:32px;border-radius:16px;background:var(--orange);color:var(--white);font-family:"Rubik",sans-serif;font-size:14px;display:flex;align-items:center;justify-content:center}
.search{left:1085px;top:48px}

/* hero */
.hero{left:0;top:112px;width:1200px;height:555px;background:linear-gradient(100deg,var(--blue-dark),var(--blue-light));overflow:hidden}
.hero h1{position:absolute;left:98px;top:152px;font-family:"Rubik",sans-serif;font-weight:700;font-size:32px;line-height:38px;color:var(--white)}
.hero p{position:absolute;left:100px;top:250px;width:430px;font-size:13px;line-height:19.5px;color:var(--white)}
.hero .btn{position:absolute;left:98px;top:356px}
.hero-art{left:620px;top:50px;width:570px;height:525px;border-radius:46% 54% 40% 60%/40% 38% 62% 60%;background:linear-gradient(160deg,#b6a9f5,#8ec9ff 70%,#6fbfff)}

/* services */
.services-eyebrow{left:0;top:727px;width:1200px;text-align:center}
.services-title{left:0;top:755px;width:1200px;text-align:center;font-size:54px}
.card{top:853px;width:338px;height:329px;border:1px solid var(--line);background:var(--white);text-align:center;padding-top:62px;box-shadow:0 4px 14px rgba(30,80,160,.08)}
.card h3{font-family:"Rubik",sans-serif;font-weight:500;font-size:23px;color:var(--blue);margin-top:16px;white-space:nowrap}
.card p{font-size:12px;line-height:20px;width:245px;margin:10px auto 0}
.card .more{display:block;margin-top:24px;font-family:"Rubik",sans-serif;font-weight:700;font-size:13px;color:var(--orange)}
.card.featured{background:linear-gradient(180deg,var(--blue-light),var(--blue-dark));border-color:var(--blue)}
.card.featured h3,.card.featured p,.card.featured .more{color:var(--white)}

.faint-mark{left:70px;top:1190px;width:1060px;text-align:center;font-family:"Rubik",sans-serif;font-weight:800;font-size:250px;line-height:250px;color:var(--pale);height:190px;overflow:hidden}

/* about */
.about{left:0;top:1380px;width:1200px;height:472px;background:var(--pale)}
.about-art{left:103px;top:81px;width:495px;height:325px;border-radius:8px;background:linear-gradient(135deg,#e6edf9,#c9dbf6)}
.about .eyebrow{position:absolute;left:641px;top:84px;font-size:14px}
.about h2{position:absolute;left:641px;top:106px;font-size:42px}
.about p{position:absolute;left:641px;top:168px;width:462px;font-size:13px;line-height:19.6px;color:#333;text-align:justify}
.about .btn{position:absolute;left:641px;top:352px}

/* testimonials */
.testimonials{left:0;top:1852px;width:1200px;height:513px;background:linear-gradient(100deg,var(--blue-dark),var(--blue-light))}
.testimonials h2{position:absolute;left:0;top:68px;width:1200px;text-align:center;color:var(--white);font-size:46px}
.quote{top:169px;width:313px;height:180px;background:var(--white);padding:50px 24px 0;text-align:center;font-size:12.5px;line-height:18px;color:#555}
.quote::after{content:"";position:absolute;left:68px;bottom:-18px;border-right:20px solid transparent;border-top:18px solid var(--white)}
.author{display:flex;align-items:center;gap:20px}
.avatar{width:64px;height:64px;border-radius:50%;background:linear-gradient(135deg,#d8dde6,#8792a3);border:2px solid var(--white)}
.author b{display:block;font-family:"Rubik",sans-serif;font-weight:700;font-size:15px;color:var(--orange)}
.author span{font-family:"Rubik",sans-serif;font-weight:500;font-size:13px;color:var(--white)}
.dots{left:569px;top:463px;display:flex;gap:4px}
.dots i{width:18px;height:5px;border-radius:3px;background:var(--white)}
.dots i:first-child{background:var(--orange)}

/* faq */
.faq-title{left:97px;top:2443px;font-size:44px;line-height:46px}
.faq-item{left:97px;width:406px;height:50px;border:1px solid var(--orange);border-radius:2px;display:flex;align-items:center;justify-content:space-between;padding:0 14px 0 17px;font-family:"Rubik",sans-serif;font-weight:500;font-size:13px;color:var(--ink);box-shadow:0 3px 8px rgba(0,0,0,.06)}
.faq-art{left:558px;top:2398px;width:534px;height:333px;border-radius:50% 50% 10px 10px/40% 40% 10px 10px;background:linear-gradient(180deg,#fff5cf,#d5dcf6)}

/* contact */
.contact-title{left:0;top:2824px;width:1200px;text-align:center;font-size:44px}
.rule{left:563px;top:2896px;width:74px;height:3px;background:#bbb}
.c-icon{top:2933px;width:50px;height:50px;border-radius:50%;background:var(--orange);display:flex;align-items:center;justify-content:center}
.contact-info{left:0;top:2999px;width:1200px;text-align:center;font-family:"Rubik",sans-serif;font-size:16px;letter-spacing:1px;color:#333;word-spacing:2px}
.field{border:1px solid var(--blue);padding:0 34px;display:flex;align-items:center;font-size:14px;color:#888}
.field.area{align-items:flex-start;padding-top:26px}
.send{left:257px;top:3389px;width:685px;height:58px;background:linear-gradient(180deg,var(--blue-light),var(--blue-dark));color:var(--white);font-family:"Rubik",sans-serif;font-weight:500;font-size:18px;display:flex;align-items:center;justify-content:center}

/* footer */
.foot-map{left:160px;top:3470px;width:880px;height:330px;border-radius:40%;background:radial-gradient(ellipse,#eef0f4 30%,transparent 70%)}
.site-footer .wordmark{left:0;top:3520px;width:1200px;text-align:center;font-size:78px}
.foot-nav{left:0;top:3642px;width:1200px;display:flex;justify-content:center;gap:34px;font-family:"Rubik",sans-serif;font-weight:500;font-size:16px;color:var(--ink)}
.socials{left:525px;top:3686px;display:flex;gap:8px}
.socials i{width:30px;height:30px;border-radius:50%;background:var(--orange)}
.foot-line{left:0;top:3740px;width:1200px;height:1px;background:#ccc}
.copyright{left:0;top:3763px;width:1200px;text-align:center;font-family:"Rubik",sans-serif;font-size:14px;color:var(--ink);letter-spacing:.5px}
</style>
</head>
<body>

<header class="site-header abs">
  <div class="wordmark abs">Zentory</div>
  <nav class="main-nav abs"><span>Home</span><span>Services Offered</span><span>About Us</span><span>Testimonials</span><span>Faq</span></nav>
  <div class="login abs">Log In</div>
  <svg class="search abs" width="16" height="16" viewBox="0 0 16 16"><circle cx="6.5" cy="6.5" r="5" fill="none" stroke="#1f6fd6" stroke-width="2"/><line x1="10.5" y1="10.5" x2="15" y2="15" stroke="#1f6fd6" stroke-width="2"/></svg>
</header>

<section class="hero abs">
  <h1>THE REAL DONE-FOR-YOU LINK<br>BUILDING SERVICE</h1>
  <p>Lorem Ipsum is simply dummy text of the printing and typesetting industry. Lorem Ipsum has been the industry's standard dummy text ever since the 1500s, when an unknown printer took a galley of type and scrambled it to make a type specimen book.</p>
  <div class="btn">LEARN MORE <svg width="20" height="20" viewBox="0 0 20 20"><circle cx="10" cy="10" r="8" fill="none" stroke="#fff" stroke-width="2"/><path d="M8 6.5l5 3.5-5 3.5z" fill="#fff"/></svg></div>
  <div class="hero-art abs" role="img" aria-label="Illustration of a man with a magnifying glass studying a web page beside a phone and plants"></div>
</section>

<div class="eyebrow services-eyebrow abs">WHAT WE OFFER</div>
<h2 class="heading services-title abs">SERVICES OFFERED</h2>

<article class="card abs" style="left:72px">
  <svg width="60" height="58" viewBox="0 0 60 58" fill="none" stroke="#f57c00" stroke-width="2"><rect x="4" y="4" width="52" height="38" rx="3"/><line x1="22" y1="52" x2="38" y2="52"/><line x1="30" y1="42" x2="30" y2="52"/><rect x="17" y="16" width="14" height="10" rx="5"/><rect x="28" y="20" width="14" height="10" rx="5"/></svg>
  <h3>Premium Links</h3>
  <p>Lorem Ipsum is simply dummy text of the printing and typesetting industry. Lorem Ipsum has been the industry's.</p>
  <span class="more">READ MORE</span>
</article>
<article class="card featured abs" style="left:430px">
  <svg width="60" height="58" viewBox="0 0 62 62" fill="none" stroke="#fff" stroke-width="2"><rect x="4" y="4" width="54" height="40" rx="3"/><line x1="4" y1="12" x2="58" y2="12"/><rect x="10" y="18" width="16" height="10"/><line x1="30" y1="20" x2="50" y2="20"/><line x1="30" y1="26" x2="46" y2="26"/><path d="M36 34v18l5-4 4 8 3-1-4-8h6z"/></svg>
  <h3>Monthly Links Subscription</h3>
  <p>Lorem Ipsum is simply dummy text of the printing and typesetting industry. Lorem Ipsum has been the industry's.</p>
  <span class="more">READ MORE</span>
</article>
<article class="card abs" style="left:793px">
  <svg width="60" height="58" viewBox="0 0 58 58" fill="none" stroke="#f57c00" stroke-width="4" stroke-linecap="round"><path d="M26 20l8-8a8 8 0 0 1 12 12l-8 8"/><path d="M32 38l-8 8a8 8 0 0 1-12-12l8-8"/><line x1="22" y1="36" x2="36" y2="22"/></svg>
  <h3>Link Insertions</h3>
  <p>Lorem Ipsum is simply dummy text of the printing and typesetting industry. Lorem Ipsum has been the industry's.</p>
  <span class="more">READ MORE</span>
</article>

<div class="faint-mark abs" aria-hidden="true">Zentory</div>

<section class="about abs">
  <div class="about-art abs" role="img" aria-label="Line illustration of a laptop with small figures, papers and a coffee cup"></div>
  <div class="eyebrow">WELCOME OUR COMPANY</div>
  <h2 class="heading">ABOUT OUR COMPANY</h2>
  <p>Lorem Ipsum is simply dummy text of the printing and typesetting industry. Lorem Ipsum has been the industry's standard dummy text ever since the 1500s, when an unknown printer took a galley of type and scrambled it to make a type specimen book. Lorem Ipsum is simply dummy text of the printing and typesetting industry. Lorem Ipsum has been the industry's standard dummy text ever since the 1500s, when an unknown printer took a galley of type and scrambled it to make a type specimen book. Lorem Ipsum is simply dummy text of the printing and typesetting.</p>
  <div class="btn">LEARN MORE <svg width="20" height="20" viewBox="0 0 20 20"><circle cx="10" cy="10" r="8" fill="none" stroke="#fff" stroke-width="2"/><path d="M8 6.5l5 3.5-5 3.5z" fill="#fff"/></svg></div>
</section>

<section class="testimonials abs">
  <h2 class="heading">TESTIMONIALS</h2>
  <blockquote class="quote abs" style="left:100px">Esse maxime tempore maiores laboriosam nobis, aut cum quidem est ab ipsam soluta voluptate totam quibusdam quo neque Lorem ipsum dolor sit amet, consectetur adipiscing elit, sed do eiusmod</blockquote>
  <blockquote class="quote abs" style="left:443px">Esse maxime tempore maiores laboriosam nobis, aut cum quidem est ab ipsam soluta voluptate totam quibusdam quo neque Lorem ipsum dolor sit amet, consectetur adipiscing elit, sed do eiusmod</blockquote>
  <blockquote class="quote abs" style="left:785px">Esse maxime tempore maiores laboriosam nobis, aut cum quidem est ab ipsam soluta voluptate totam quibusdam quo neque Lorem ipsum dolor sit amet, consectetur adipiscing elit, sed do eiusmod</blockquote>
  <div class="author abs" style="left:98px;top:364px"><div class="avatar" role="img" aria-label="Client portrait"></div><div><b>DANA HOLT</b><span>Project Manager</span></div></div>
  <div class="author abs" style="left:441px;top:364px"><div class="avatar" role="img" aria-label="Client portrait"></div><div><b>DANA HOLT</b><span>Project Manager</span></div></div>
  <div class="author abs" style="left:783px;top:364px"><div class="avatar" role="img" aria-label="Client portrait"></div><div><b>DANA HOLT</b><span>Project Manager</span></div></div>
  <div class="dots abs"><i></i><i></i><i></i></div>
</section>

<h2 class="heading faq-title abs">FREQUENTLY<br>ASK QUESTION</h2>
<div class="faq-item abs" style="top:2564px">Lorem Ipsum is simply dummy text of the printing<svg width="18" height="18" viewBox="0 0 18 18"><circle cx="9" cy="9" r="7.5" fill="none" stroke="#f57c00" stroke-width="1.5"/><path d="M6 7.5l3 3 3-3" fill="none" stroke="#f57c00" stroke-width="1.5"/></svg></div>
<div class="faq-item abs" style="top:2619px">Lorem Ipsum is simply dummy text of the printing<svg width="18" height="18" viewBox="0 0 18 18"><circle cx="9" cy="9" r="7.5" fill="none" stroke="#f57c00" stroke-width="1.5"/><path d="M6 7.5l3 3 3-3" fill="none" stroke="#f57c00" stroke-width="1.5"/></svg></div>
<div class="faq-item abs" style="top:2675px">Lorem Ipsum is simply dummy text of the printing<svg width="18" height="18" viewBox="0 0 18 18"><circle cx="9" cy="9" r="7.5" fill="none" stroke="#f57c00" stroke-width="1.5"/><path d="M6 7.5l3 3 3-3" fill="none" stroke="#f57c00" stroke-width="1.5"/></svg></div>
<div class="faq-art abs" role="img" aria-label="Illustration of people gathered around large yellow question and exclamation marks"></div>

<h2 class="heading contact-title abs">CONTACT US</h2>
<div class="rule abs"></div>
<div class="c-icon abs" style="left:366px"><svg width="20" height="24" viewBox="0 0 20 24"><path d="M10 1a8 8 0 0 0-8 8c0 6 8 14 8 14s8-8 8-14a8 8 0 0 0-8-8z" fill="#fff"/><circle cx="10" cy="9" r="3" fill="#f57c00"/></svg></div>
<div class="c-icon abs" style="left:578px"><svg width="22" height="22" viewBox="0 0 24 24"><path d="M6.6 10.8a15 15 0 0 0 6.6 6.6l2.2-2.2a1 1 0 0 1 1-.25 11.4 11.4 0 0 0 3.6.57 1 1 0 0 1 1 1V20a1 1 0 0 1-1 1A17 17 0 0 1 3 4a1 1 0 0 1 1-1h3.5a1 1 0 0 1 1 1c0 1.25.2 2.45.57 3.57a1 1 0 0 1-.25 1z" fill="#fff"/></svg></div>
<div class="c-icon abs" style="left:793px"><svg width="22" height="16" viewBox="0 0 22 16"><rect x="1" y="1" width="20" height="14" rx="1" fill="#fff"/><path d="M1 2l10 7 10-7" fill="none" stroke="#f57c00" stroke-width="1.5"/></svg></div>
<div class="contact-info abs">Halvern, Westmarch &nbsp;&nbsp; | &nbsp;&nbsp; 0147-882-3096 &nbsp;&nbsp; | &nbsp;&nbsp; hello@zentorymail.com</div>

<form class="contact-form">
  <div class="field abs" style="left:257px;top:3049px;width:685px;height:58px">Your Name*</div>
  <div class="field abs" style="left:257px;top:3126px;width:335px;height:58px">Your Phone*</div>
  <div class="field abs" style="left:606px;top:3126px;width:336px;height:58px">Your E-mail address*</div>
  <div class="field area abs" style="left:257px;top:3204px;width:685px;height:163px">Your Message</div>
  <div class="send abs">SEND MESSAGE</div>
</form>

<footer class="site-footer">
  <div class="foot-map abs" role="img" aria-label="Faint dotted world map"></div>
  <div class="wordmark abs">Zentory</div>
  <nav class="foot-nav abs"><span>Home</span><span>Services Offered</span><span>About Us</span><span>Testimonials</span><span>Faq</span></nav>
  <div class="socials abs"><i></i><i></i><i></i><i></i></div>
  <div class="foot-line abs"></div>
  <div class="copyright abs">COPYRIGHT © 2021 ZENTORY. ALL RIGHTS RESERVED</div>
</footer>

</body>
</html>
```